Brenlow Estates Website and Logo Design

We need a new logo and website designed for 'Brenlow Estates Ltd', which is a well established Guernsey property holding company founded in 1934.

The company does not currently have a website. The new website should be similar in style and layout to https://www.quorvanhall.example/.

Target Market(s)

Industry, Media, Tenants

Industry/Entity Type

Property Management

Logo Text

BEL OR Brenlow Estates Ltd OR BE

Coding

Coded - Design and coding required

Number of Pages Required

4 page

Font styles to use
Other font styles liked:
• Helvetica

Requirements
Must have
• The logo laying over the picture (like https://www.quorvanhall.example/).
• Big pictures on homepage (like https://www.quorvanhall.example/)

```html
<!DOCTYPE html>
<html lang="en">
<head>
<meta charset="utf-8">
<title>Brenlow Estates Ltd</title>
<link href="https://fonts.googleapis.com/css2?family=Alegreya+SC:ital,wght@0,400;0,500;0,700;1,500&family=Arimo:ital,wght@0,400;1,400&display=swap" rel="stylesheet">
<style>
:root{
  --teal:#1fc1b5;
  --teal-dark:#17a99f;
  --ink:#222;
  --body:#6b6b6b;
  --band:#1d2631;
  --footer:#121c1e;
  --white:#fff;
}
*{box-sizing:border-box;margin:0;padding:0}
html,body{width:1200px;height:4045px;overflow:hidden}
body{font-family:"Arimo",Helvetica,Arial,sans-serif;color:var(--body);background:var(--white);position:relative}
section,header,footer{position:absolute;left:0;width:1200px}
.photo{position:absolute;inset:0}
.btn{display:block;position:absolute;background:var(--teal);color:var(--white);border-radius:28px;font-family:"Alegreya SC",Georgia,serif;font-size:22px;text-align:center;text-decoration:none}

/* hero */
.hero{top:0;height:674px}
.hero .photo{background:linear-gradient(180deg,#4a5562 0%,#6d7784 35%,#5d6a78 60%,#2f3d4d 100%)}
.brand{position:absolute;left:80px;top:38px;display:flex;align-items:center;gap:14px;color:var(--teal);font-family:"Alegreya SC",Georgia,serif;font-size:38px;text-decoration:none}
.brand-mark{width:58px;height:58px;border-radius:50%;background:var(--teal)}
.nav{position:absolute;top:54px;left:561px;display:flex;list-style:none}
.nav a{display:block;height:46px;line-height:46px;color:var(--white);text-decoration:none;font-size:18px}
.nav .current a{background:var(--teal);border-radius:24px;padding:0 26px;margin-right:42px}
.nav li:nth-child(2) a{margin-right:48px}
.nav li:nth-child(3) a{margin-right:44px}
.nav li:nth-child(4) a{margin-right:36px}
.hero h1{position:absolute;top:280px;width:100%;text-align:center;color:var(--white);font-family:"Alegreya SC",Georgia,serif;font-weight:400;font-size:66px;letter-spacing:1px}
.hero p{position:absolute;top:372px;left:110px;width:980px;text-align:center;color:var(--white);font-size:16px;line-height:27px}
.hero .btn{left:507px;top:445px;width:186px;height:54px;line-height:54px}

/* intro text blocks */
.intro{text-align:center}
.intro h2{font-family:"Alegreya SC",Georgia,serif;font-weight:400;color:var(--teal);font-size:44px;line-height:52px}
.intro p{width:920px;margin:0 auto 10px;font-size:14px;line-height:26px}
.intro .btn{position:relative;left:auto;top:auto;margin:16px auto 0;width:186px;height:56px;line-height:56px}
.welcome{top:674px;height:437px;padding-top:56px}
.welcome h2{margin-bottom:14px}

/* heading bands */
.band{height:168px;background:var(--band)}
.band .photo{background:linear-gradient(180deg,#2a3440 0%,#1b242e 60%,#232d38 100%)}
.band h2{position:relative;line-height:168px;text-align:center;font-family:"Alegreya SC",Georgia,serif;font-weight:400;color:var(--teal);font-size:44px}

/* what we do */
.services{top:1281px;height:412px}
.card{position:absolute;top:48px;width:335px;height:302px}
.card .pic{height:240px}
.card h3{height:62px;line-height:62px;background:var(--teal);color:var(--white);text-align:center;font-family:"Alegreya SC",Georgia,serif;font-weight:500;font-size:24px}

/* projects */
.projects{top:1861px;height:512px}
.project{position:absolute;top:27px;width:494px}
.project .pic{height:256px}
.project h3{margin-top:30px;font-family:"Alegreya SC",Georgia,serif;font-weight:500;color:var(--ink);font-size:21px;white-space:nowrap}
.project p{margin-top:6px;font-size:14px;line-height:26px}
.more{display:inline-block;margin-top:8px;color:var(--teal);font-family:"Alegreya SC",Georgia,serif;font-weight:500;font-size:15px;text-decoration:none}

/* about */
.about{top:2540px;height:353px;padding-top:36px}

/* news */
.news{top:3061px;height:418px}
.post{position:absolute;top:43px;width:248px}
.post .pic{height:162px}
.post h3{margin-top:22px;font-family:"Alegreya SC",Georgia,serif;font-weight:500;font-style:italic;color:var(--ink);font-size:16px;white-space:nowrap}
.post .date{margin-top:10px;display:flex;align-items:center;gap:8px;color:var(--teal);font-style:italic;font-size:14px}
.post p{margin-top:8px;font-size:14px;line-height:26px}

/* footer */
.site-footer{top:3479px;height:566px;color:#c9cfd0}
.site-footer .photo{background:linear-gradient(180deg,#1a2a2c 0%,#132022 50%,#0f1a1b 100%)}
.subscribe h2{position:absolute;top:50px;width:100%;text-align:center;font-family:"Alegreya SC",Georgia,serif;font-weight:400;color:var(--teal);font-size:44px}
.subscribe .field{position:absolute;left:267px;top:132px;width:477px;height:54px;border:1px solid #5b6768;color:#9aa4a5;font-style:italic;font-size:14px;line-height:52px;padding-left:22px}
.subscribe .btn{left:766px;top:132px;width:167px;height:54px;line-height:54px}
.col{position:absolute;top:266px}
.col h4{font-family:"Alegreya SC",Georgia,serif;font-weight:500;color:var(--teal);font-size:19px;margin-bottom:14px}
.col p{font-size:14px;line-height:25px}
.about-col{left:81px;width:300px}
.social{display:flex;gap:9px;margin-top:20px}
.social a{width:42px;height:42px;border-radius:50%;background:var(--teal);display:flex;align-items:center;justify-content:center}
.sitemap{left:434px}
.sitemap ul{list-style:none}
.sitemap li{font-size:14px;line-height:25px}
.sitemap li::before{content:"\00BB";color:#c9cfd0;margin-right:14px}
.sitemap li.current{color:var(--teal)}
.contact-col{left:790px;width:330px}
.contact-row{display:flex;gap:22px;align-items:flex-start;margin-bottom:20px}
.contact-row svg{flex:none;margin-top:4px}
.contact-row b{display:block;font-family:"Alegreya SC",Georgia,serif;font-weight:500;color:var(--teal);font-size:15px;margin-bottom:4px}
.copyright{position:absolute;top:504px;left:81px;width:1038px;border-top:1px solid #334042;padding-top:20px;text-align:center;font-size:14px}
.copyright em{font-style:normal;color:var(--teal)}
</style>
</head>
<body>

<header class="hero">
  <div class="photo" role="img" aria-label="City waterfront skyline at dusk"></div>
  <a class="brand" href="#"><span class="brand-mark"></span>Brenlow Estates Ltd</a>
  <ul class="nav">
    <li class="current"><a href="#">HOME</a></li>
    <li><a href="#">ABOUT</a></li>
    <li><a href="#">PROJECTS</a></li>
    <li><a href="#">NEWS</a></li>
    <li><a href="#">CONTACT</a></li>
  </ul>
  <h1>BRENLOW ESTATES LTD</h1>
  <p>Brenlow Estates Limited (BEL) is a family-owned Guernsey property holding company. It purchases properties that are considered to have potential for development either through refurbishment.</p>
  <a class="btn" href="#">Contact Us</a>
</header>

<section class="welcome intro">
  <h2>Welcome to Brenlow Estates Ltd</h2>
  <p>Brenlow Estates Limited (BEL) is a family-owned Guernsey property holding company. It purchases properties that are considered to have potential for development either through refurbishment or by obtaining planning permission to change its classification from, for example, industrial premises to offices or retail outlets, or by the marriage value of buying.</p>
  <p>BEL's reputation as a fair-minded landlord stems from the application of the founder's tenet of working with the tenant to help maximise the business benefits of both parties.</p>
  <p>There is no capital gains tax on the sale of property in the island which makes buying and selling an attractive enterprise.</p>
  <a class="btn" href="#">Know More</a>
</section>

<section class="band" style="top:1111px">
  <div class="photo" role="img" aria-label="Darkened city skyline banner"></div>
  <h2>What We Do</h2>
</section>

<section class="services">
  <div class="card" style="left:76px">
    <div class="pic" role="img" aria-label="Harbour town with moored boats under blue sky" style="background:linear-gradient(180deg,#8fbfe6 0%,#cfd6d2 45%,#3c86a8 70%,#1f5f84 100%)"></div>
    <h3>Yesterday</h3>
  </div>
  <div class="card" style="left:431px">
    <div class="pic" role="img" aria-label="City towers on a harbour beneath mountains" style="background:linear-gradient(180deg,#a9c4de 0%,#6f7b8c 40%,#3c4a5a 65%,#1d3a55 100%)"></div>
    <h3>Today</h3>
  </div>
  <div class="card" style="left:787px">
    <div class="pic" role="img" aria-label="Marina with boats and hillside houses" style="background:linear-gradient(180deg,#8cc3ec 0%,#c8d2c6 40%,#4c8db0 65%,#2b6a8c 100%)"></div>
    <h3>Tomorrow</h3>
  </div>
</section>

<section class="band" style="top:1693px">
  <div class="photo" role="img" aria-label="Darkened harbour banner"></div>
  <h2>Our Projects</h2>
</section>

<section class="projects">
  <article class="project" style="left:94px">
    <div class="pic" role="img" aria-label="Sailing boats in a marina at sunset" style="background:linear-gradient(180deg,#6b6f94 0%,#c99aa8 40%,#d8b3a8 55%,#5e6a86 100%)"></div>
    <h3>Lorem Ipsum is simply dummy text of the</h3>
    <p>Lorem Ipsum is simply dummy text of the printing and typesetting industry. Lorem Ipsum has been the industry's standard dummy text ever since the 1500s, when an unknown printer took a galley of type</p>
    <a class="more" href="#">Read More...&raquo;</a>
  </article>
  <article class="project" style="left:612px">
    <div class="pic" role="img" aria-label="Illuminated harbour town at night" style="background:linear-gradient(180deg,#2e5c9a 0%,#3b6aa4 40%,#c97a3a 62%,#1f3a66 100%)"></div>
    <h3>Lorem Ipsum is simply dummy text of the</h3>
    <p>Lorem Ipsum is simply dummy text of the printing and typesetting industry. Lorem Ipsum has been the industry's standard dummy text ever since the 1500s, when an unknown printer took a galley of type</p>
    <a class="more" href="#">Read More...&raquo;</a>
  </article>
</section>

<section class="band" style="top:2373px">
  <div class="photo" role="img" aria-label="Darkened waterfront banner"></div>
  <h2>About Us</h2>
</section>

<section class="about intro">
  <p>Brenlow Estates Limited (BEL) is a family-owned Guernsey property holding company. It purchases properties that are considered to have potential for development either through refurbishment or by obtaining planning permission to change its classification from, for example, industrial premises to offices or retail outlets, or by the marriage value of buying.</p>
  <p>BEL's reputation as a fair-minded landlord stems from the application of the founder's tenet of working with the tenant to help maximise the business benefits of both parties.</p>
  <p>There is no capital gains tax on the sale of property in the island which makes buying and selling an attractive enterprise.</p>
  <a class="btn" href="#">Know More</a>
</section>

<section class="band" style="top:2893px">
  <div class="photo" role="img" aria-label="Darkened city skyline banner"></div>
  <h2>Latest News</h2>
</section>

<section class="news">
  <article class="post" style="left:78px">
    <div class="pic" role="img" aria-label="Yachts moored in a calm marina" style="background:linear-gradient(180deg,#5d8fc8 0%,#9ab8d8 45%,#2f5f93 100%)"></div>
    <h3>Lorem Ipsum is simple text</h3>
    <div class="date"><svg width="14" height="14" viewBox="0 0 14 14"><rect x="1" y="2" width="12" height="11" fill="none" stroke="currentColor" stroke-width="1.5"/><line x1="1" y1="5.5" x2="13" y2="5.5" stroke="currentColor" stroke-width="1.5"/></svg>Posted by 1 Dec.</div>
    <p>Lorem Ipsum is simply dummy text of the printing and</p>
  </article>
  <article class="post" style="left:342px">
    <div class="pic" role="img" aria-label="Aerial view of a harbour town" style="background:linear-gradient(180deg,#7fb0d8 0%,#b7c3c4 45%,#4f7fa4 100%)"></div>
    <h3>Lorem Ipsum is simple text</h3>
    <div class="date"><svg width="14" height="14" viewBox="0 0 14 14"><rect x="1" y="2" width="12" height="11" fill="none" stroke="currentColor" stroke-width="1.5"/><line x1="1" y1="5.5" x2="13" y2="5.5" stroke="currentColor" stroke-width="1.5"/></svg>Posted by 1 Dec.</div>
    <p>Lorem Ipsum is simply dummy text of the printing and typesetting ind - ustry Lorem Ipsum has.</p>
  </article>
  <article class="post" style="left:609px">
    <div class="pic" role="img" aria-label="Harbour at sunset with orange sky" style="background:linear-gradient(180deg,#3a4c7a 0%,#d2783a 45%,#6a3a2e 70%,#223050 100%)"></div>
    <h3>Lorem Ipsum is simple text</h3>
    <div class="date"><svg width="14" height="14" viewBox="0 0 14 14"><rect x="1" y="2" width="12" height="11" fill="none" stroke="currentColor" stroke-width="1.5"/><line x1="1" y1="5.5" x2="13" y2="5.5" stroke="currentColor" stroke-width="1.5"/></svg>Posted by 1 Dec.</div>
    <p>Lorem Ipsum is simply dummy text of the printing and typesetting ind - ustry Lorem Ipsum has.</p>
  </article>
  <article class="post" style="left:874px">
    <div class="pic" role="img" aria-label="Marina at twilight with boat masts" style="background:linear-gradient(180deg,#3a5ea8 0%,#6c8ccc 45%,#2a4a8a 100%)"></div>
    <h3>Lorem Ipsum is simple text</h3>
    <div class="date"><svg width="14" height="14" viewBox="0 0 14 14"><rect x="1" y="2" width="12" height="11" fill="none" stroke="currentColor" stroke-width="1.5"/><line x1="1" y1="5.5" x2="13" y2="5.5" stroke="currentColor" stroke-width="1.5"/></svg>Posted by 1 Dec.</div>
    <p>Lorem Ipsum is simply dummy text of the printing and typesetting ind - ustry Lorem Ipsum has.</p>
  </article>
</section>

<footer class="site-footer">
  <div class="photo" role="img" aria-label="Dark aerial view of a harbour city"></div>
  <div class="subscribe">
    <h2>Subscribe to Newsletter</h2>
    <div class="field">Enter Your Email Id *</div>
    <a class="btn" href="#">Subscribe</a>
  </div>
  <div class="col about-col">
    <h4>About Us</h4>
    <p>Brenlow Estates Limited (BEL) is a family-owned Guernsey property holding company. It purchases properties that are considered to have potential for development either through.</p>
    <div class="social">
      <a href="#" aria-label="Share"><svg width="18" height="18" viewBox="0 0 18 18"><circle cx="4" cy="9" r="2.3" fill="#fff"/><circle cx="14" cy="4" r="2.3" fill="#fff"/><circle cx="14" cy="14" r="2.3" fill="#fff"/><path d="M4 9l10-5M4 9l10 5" stroke="#fff" stroke-width="1.4"/></svg></a>
      <a href="#" aria-label="Email"><svg width="18" height="14" viewBox="0 0 18 14"><rect x="1" y="1" width="16" height="12" fill="none" stroke="#fff" stroke-width="1.6"/><path d="M1 1l8 6 8-6" fill="none" stroke="#fff" stroke-width="1.6"/></svg></a>
      <a href="#" aria-label="Phone"><svg width="16" height="16" viewBox="0 0 18 18"><path d="M4 1.5l3 3.5-1.8 2.2a10 10 0 0 0 5.6 5.6L13 11l3.5 3-1.6 2.4C8 16 2 10 1.6 3.1z" fill="#fff"/></svg></a>
    </div>
  </div>
  <div class="col sitemap">
    <h4>Sitemap</h4>
    <ul>
      <li class="current">Home</li>
      <li>About</li>
      <li>Project</li>
      <li>News</li>
      <li>Contact</li>
    </ul>
  </div>
  <div class="col contact-col">
    <h4>Get In Touch</h4>
    <div class="contact-row">
      <svg width="18" height="24" viewBox="0 0 18 24"><path d="M9 1a7.5 7.5 0 0 0-7.5 7.5C1.5 14 9 23 9 23s7.5-9 7.5-14.5A7.5 7.5 0 0 0 9 1z" fill="none" stroke="#1fc1b5" stroke-width="1.6"/><circle cx="9" cy="8.5" r="2.6" fill="none" stroke="#1fc1b5" stroke-width="1.6"/></svg>
      <p><b>Brenlow Estates Ltd</b>101 - Lorem Ipsum is simple dummy text of print and type setting industry simple text of print and type setting.</p>
    </div>
    <div class="contact-row">
      <svg width="18" height="18" viewBox="0 0 18 18"><path d="M4 1.5l3 3.5-1.8 2.2a10 10 0 0 0 5.6 5.6L13 11l3.5 3-1.6 2.4C8 16 2 10 1.6 3.1z" fill="none" stroke="#1fc1b5" stroke-width="1.5" stroke-linejoin="round"/></svg>
      <p>123 456 7890</p>
    </div>
    <div class="contact-row">
      <svg width="20" height="15" viewBox="0 0 20 15"><rect x="1" y="1" width="18" height="13" fill="none" stroke="#1fc1b5" stroke-width="1.5"/><path d="M1 1l9 7 9-7" fill="none" stroke="#1fc1b5" stroke-width="1.5"/></svg>
      <p>info@BrenlowEstates.example</p>
    </div>
  </div>
  <div class="copyright">&copy;<em>Brenlow Estates Ltd</em> - 2016. All Rights Reserved</div>
</footer>

</body>
</html>
```